Business Card Design for Flood Rescue 360 - Property Restoration Professionals

I need a business card designed for Flood Rescue 360. We are a full-service property restoration solution. Providing water, fire, smoke & storm restoration as well as mold remediation and full remodel or reconstruction to homes and businesses across Dallas-Fort Worth, TX.
Target Market(s)
home and business owners with insurance covered property damage from water, fire or storm related damage
Industry/Entity Type
property restoration
Contact Information for Business Card
Marcus Pelley General Manager Cell: 214-555-0193 Office: 469-555-0148 email: Marcus@FloodRescue360.example services: Water, Fire, Mold, Reconstruction Tagline: Urgency for Your Water Emergency!
Look and feel
Each slider illustrates characteristics of the customer's brand and the style your logo design should communicate.

```html
<!DOCTYPE html>
<html lang="en">
<head>
<meta charset="utf-8">
<title>Flood Rescue 360 – Business Card</title>
<link rel="stylesheet" href="https://fonts.googleapis.com/css2?family=Poppins:wght@500;700&family=Lato:wght@400;700&display=swap">
<style>
  :root {
    --bg: #e9eaec;
    --card-white: #ffffff;
    --card-dark: #232325;
    --brand-blue: #08a8e0;
    --ink-gray: #555659;
    --soft-gray: #8b8c8f;
    --black-tab: #1a1a1c;
    --line: #e2e3e5;
    --white: #ffffff;
  }
  * { box-sizing: border-box; margin: 0; padding: 0; }
  html, body { width: 1200px; height: 952px; overflow: hidden; }
  body {
    background: var(--bg);
    font-family: "Lato", sans-serif;
    position: relative;
  }
  .card {
    position: absolute;
    left: 250px;
    width: 700px;
    height: 400px;
    overflow: hidden;
    box-shadow: 0 10px 30px rgba(0,0,0,.18);
  }
  /* Front */
  .card-front { top: 56px; background: var(--card-white); }
  .corner-tab { position: absolute; background: var(--black-tab); }
  .corner-tab.top-left { left: 0; top: 0; width: 26px; height: 170px; }
  .corner-tab.bottom-right { right: 0; bottom: 0; width: 26px; height: 170px; }
  .brand-block { position: absolute; left: 70px; top: 110px; width: 300px; }
  .brand-name {
    font-family: "Lato", sans-serif;
    font-weight: 700;
    font-size: 44px;
    line-height: 1;
    color: var(--brand-blue);
    text-transform: uppercase;
    letter-spacing: .5px;
  }
  .brand-name span { display: block; }
  .tagline {
    margin-top: 34px;
    font-size: 15px;
    font-weight: 700;
    color: var(--ink-gray);
    text-transform: uppercase;
    letter-spacing: .3px;
  }
  .divider {
    position: absolute;
    left: 385px; top: 90px;
    width: 1px; height: 220px;
    background: var(--line);
  }
  .contact-block { position: absolute; left: 415px; top: 118px; }
  .person-name {
    font-family: "Poppins", sans-serif;
    font-weight: 500;
    font-size: 27px;
    color: var(--brand-blue);
    text-transform: uppercase;
    letter-spacing: 1px;
  }
  .person-role { font-size: 17px; color: var(--soft-gray); margin-bottom: 18px; }
  .contact-list { list-style: none; }
  .contact-list li {
    display: flex; align-items: center; gap: 10px;
    font-size: 15px; color: var(--ink-gray); line-height: 28px;
  }
  .contact-list svg { width: 14px; height: 14px; fill: var(--brand-blue); flex: none; }
  /* Back */
  .card-back { top: 496px; background: var(--card-dark); }
  .back-brand {
    position: absolute; left: 90px; top: 120px;
    display: flex; align-items: center; gap: 18px;
  }
  .back-brand-name {
    font-family: "Poppins", sans-serif;
    font-weight: 700;
    font-size: 46px;
    line-height: 1.05;
    color: var(--brand-blue);
  }
  .back-brand-dot { width: 26px; height: 26px; border-radius: 50%; background: var(--brand-blue); }
  .service-list {
    position: absolute; left: 420px; top: 220px;
    list-style: none;
    font-family: "Poppins", sans-serif;
    font-weight: 500;
    font-size: 17px;
    color: var(--white);
    line-height: 27px;
  }
  .service-list li::before {
    content: ""; display: inline-block;
    width: 5px; height: 5px; border-radius: 50%;
    background: var(--brand-blue);
    margin-right: 8px; vertical-align: middle;
  }
</style>
</head>
<body>
  <section class="card card-front" aria-label="Business card front">
    <div class="corner-tab top-left"></div>
    <div class="corner-tab bottom-right"></div>
    <div class="brand-block">
      <h1 class="brand-name"><span>Flood</span><span>Rescue 360</span></h1>
      <p class="tagline">Urgency for your water emergency!</p>
    </div>
    <div class="divider"></div>
    <div class="contact-block">
      <h2 class="person-name">Marcus Pelley</h2>
      <p class="person-role">General Manager</p>
      <ul class="contact-list">
        <li><svg viewBox="0 0 24 24"><path d="M6.6 10.8a15.1 15.1 0 0 0 6.6 6.6l2.2-2.2c.3-.3.7-.4 1-.2 1.1.4 2.3.6 3.6.6.6 0 1 .4 1 1V20c0 .6-.4 1-1 1A17 17 0 0 1 3 4c0-.6.4-1 1-1h3.5c.6 0 1 .4 1 1 0 1.3.2 2.5.6 3.6.1.3 0 .7-.2 1z"/></svg>214-555-0193</li>
        <li><svg viewBox="0 0 24 24"><path d="M2 5h20v14H2z M4 7v1l8 5 8-5V7l-8 5z" fill-rule="evenodd"/></svg>Marcus@FloodRescue360.example</li>
        <li><svg viewBox="0 0 24 24"><circle cx="12" cy="12" r="10"/></svg>www.floodrescue360.example</li>
      </ul>
    </div>
  </section>

  <section class="card card-back" aria-label="Business card back">
    <div class="back-brand">
      <p class="back-brand-name">Flood<br>Rescue 360</p>
      <div class="back-brand-dot"></div>
    </div>
    <ul class="service-list">
      <li>Water</li>
      <li>Fire</li>
      <li>Mold</li>
      <li>Reconstruction</li>
    </ul>
  </section>
</body>
</html>
```